RevelHubQZ Business Cards

Front
Has logo with a design. Website address (www.revelhubqz-example.net)
Has slogan (discover the nightlife)
Has phone number (5182297734)
Should be bold and stands out.

Back
Has details about what we offer.

Events
Search upcoming events
Submit events
Party Image Gallery
View and download HQ party images
Sign up as a contributing event photographer and get paid!
Tickets
Sell your event tickets online for free!
Direct pay
No ticket fee

Target Market(s)

These cards will be handed out in clubs and events to patrons.

Industry/Entity Type

Business

Contact Information for Business Card

Should match or mirror our website in some sort of way. Visit the website to get ideas.

Requirements
Must have
• Must be designed for a 3x3 inch card.

```html
<!DOCTYPE html>
<html lang="en">
<head>
<meta charset="utf-8">
<title>RevelHubQZ Business Cards</title>
<link rel="stylesheet" href="https://fonts.googleapis.com/css2?family=Comfortaa:wght@700&family=Roboto+Condensed:wght@400;700&family=Dosis:wght@500;700&display=swap">
<style>
  :root {
    --stage-dark: #151515;
    --stage-light: #4a4a4a;
    --card-white: #ffffff;
    --card-dark: #4b4b4d;
    --brand-blue: #2fa7dd;
    --brand-pink: #e4338f;
    --text-grey: #4a4a4a;
    --text-light: #f2f2f2;
  }
  * { box-sizing: border-box; margin: 0; padding: 0; }
  html, body { width: 1200px; height: 950px; overflow: hidden; }
  body {
    background: radial-gradient(ellipse at 50% 35%, var(--stage-light) 0%, var(--stage-dark) 75%);
    display: flex;
    align-items: center;
    justify-content: center;
    gap: 70px;
  }
  .card {
    position: relative;
    width: 460px;
    height: 460px;
    overflow: hidden;
    box-shadow: 0 18px 40px rgba(0,0,0,.55);
  }

  /* Front */
  .card--front { background: var(--card-white); }
  .brand {
    position: absolute;
    top: 70px;
    left: 46px;
    display: flex;
    align-items: center;
    gap: 14px;
  }
  .brand__dot {
    width: 30px; height: 30px;
    border-radius: 50%;
    background: var(--brand-blue);
  }
  .brand__name {
    font-family: "Comfortaa", sans-serif;
    font-weight: 700;
    font-size: 40px;
    color: var(--brand-blue);
    letter-spacing: -0.5px;
  }
  .brand__slogan {
    position: absolute;
    top: 122px;
    left: 92px;
    font-family: "Dosis", sans-serif;
    font-weight: 500;
    font-size: 13px;
    letter-spacing: 4px;
    color: var(--brand-pink);
  }
  .contact {
    position: absolute;
    left: 46px;
    bottom: 80px;
    width: 368px;
  }
  .contact__icon {
    display: block;
    margin: 0 auto 22px;
    width: 40px; height: 40px;
  }
  .contact__phone {
    font-family: "Roboto Condensed", sans-serif;
    font-weight: 700;
    font-size: 62px;
    line-height: 1;
    color: var(--brand-blue);
    letter-spacing: 1px;
  }
  .contact__web {
    margin-top: 8px;
    font-family: "Roboto Condensed", sans-serif;
    font-weight: 700;
    font-size: 21px;
    color: var(--text-grey);
    letter-spacing: 0.6px;
  }
  .edge-band {
    position: absolute;
    left: 0; right: 0; bottom: 0;
    height: 16px;
    display: flex;
  }
  .edge-band__blue { flex: 0 0 60%; background: var(--brand-blue); }
  .edge-band__pink { flex: 0 0 22%; background: var(--brand-pink); }
  .edge-band__rest { flex: 1; background: var(--card-white); }

  /* Back */
  .card--back { background: var(--card-dark); }
  .offer {
    position: absolute;
    top: 70px;
    left: 30px;
    right: 30px;
    text-align: center;
  }
  .offer__title {
    font-family: "Dosis", sans-serif;
    font-weight: 700;
    font-size: 30px;
    color: var(--brand-blue);
    margin-bottom: 22px;
  }
  .offer__list {
    list-style: none;
    font-family: "Dosis", sans-serif;
    font-weight: 500;
    font-size: 19px;
    line-height: 1.55;
    color: var(--text-light);
  }
  .offer__sep {
    display: inline-block;
    width: 7px; height: 7px;
    margin: 0 6px 3px;
    background: var(--brand-pink);
    vertical-align: middle;
  }
  .equalizer {
    position: absolute;
    left: 0; right: 0; bottom: 0;
    height: 70px;
    background: linear-gradient(180deg, var(--brand-pink) 0%, var(--brand-blue) 100%);
    opacity: .85;
  }
</style>
</head>
<body>

  <section class="card card--front" aria-label="Card front">
    <div class="brand">
      <span class="brand__dot"></span>
      <span class="brand__name">RevelHubQZ</span>
    </div>
    <p class="brand__slogan">discover the nightlife</p>

    <div class="contact">
      <svg class="contact__icon" viewBox="0 0 40 40" aria-hidden="true">
        <circle cx="20" cy="20" r="17" fill="none" stroke="var(--brand-pink)" stroke-width="3"/>
        <path d="M14 12c1-1 2-1 3 0l2 3c.5 1 .3 1.7-.5 2.4l-1 .8c.8 2 2.4 3.6 4.4 4.4l.8-1c.7-.8 1.4-1 2.4-.5l3 2c1 1 1 2 0 3l-1.5 1.3C23 29 11 17 12.7 13.5z" fill="var(--brand-pink)"/>
      </svg>
      <p class="contact__phone">5182297734</p>
      <p class="contact__web">www.revelhubqz-example.net</p>
    </div>

    <div class="edge-band" aria-hidden="true">
      <span class="edge-band__blue"></span>
      <span class="edge-band__pink"></span>
      <span class="edge-band__rest"></span>
    </div>
  </section>

  <section class="card card--back" aria-label="Card back">
    <div class="offer">
      <h2 class="offer__title">Events</h2>
      <ul class="offer__list">
        <li>Sell your event tickets online for free!</li>
        <li>View &amp; download HQ party images</li>
        <li>Sign up as a contributing event</li>
        <li>photographer &amp; get paid!<span class="offer__sep"></span>Tickets</li>
        <li>Submit events<span class="offer__sep"></span>Direct pay</li>
        <li>Party Image Gallery<span class="offer__sep"></span>No ticket fee</li>
        <li>Search upcoming events</li>
      </ul>
    </div>
    <div class="equalizer" role="img" aria-label="Pink and blue equalizer bar pattern along the card edge"></div>
  </section>

</body>
</html>
```